Income Tax Flyer - Updates Needed

Just need to update this flyer design and give it a new look. We would like to keep all the same wording but make it stand out a little more. Our selling point is the "Same Day Tax Advance up to $6,000"

Lending, Small Loans, Tax Services, Title Loans, Personal Loans

```html
<!DOCTYPE html>
<html lang="en">
<head>
<meta charset="UTF-8">
<title>Same Day Tax Advance Flyer</title>
<link rel="stylesheet" href="https://fonts.googleapis.com/css2?family=Oswald:wght@300;400;500;600&display=swap">
<style>
  :root {
    --green: #0d5130;
    --red: #c21f28;
    --white: #ffffff;
    --paper: #ffffff;
    --dot-tone: #e4e7e3;
    --address-grey: #7a7a7a;
    --photo-hair: #5a4a3e;
    --photo-skin: #d9a98e;
    --photo-bills: #c9ccc8;
  }
  html, body {
    margin: 0;
    padding: 0;
    width: 848px;
    height: 1200px;
    overflow: hidden;
    background: var(--paper);
  }
  .flyer {
    display: block;
    width: 848px;
    height: 1200px;
  }
  .type {
    font-family: "Oswald", "Arial Narrow", sans-serif;
  }
  .headline-small { font-weight: 600; font-size: 86px; fill: var(--green); }
  .headline-tax { font-weight: 600; font-size: 218px; fill: var(--green); }
  .headline-advance { font-weight: 500; font-size: 68px; fill: var(--green); }
  .headline-amount { font-weight: 600; font-size: 168px; fill: var(--red); }
  .band-intro { font-weight: 300; font-size: 40px; fill: var(--white); }
  .band-offer { font-weight: 500; font-size: 50px; fill: var(--white); }
  .contact-title { font-weight: 500; font-size: 40px; fill: var(--green); }
  .contact-phone { font-weight: 500; font-size: 50px; fill: var(--red); }
  .address-line { font-weight: 400; font-size: 22px; fill: var(--address-grey); }
  .brand-name { font-weight: 500; font-size: 44px; fill: var(--green); }
  .brand-mark { fill: var(--red); }
  .shape-green { fill: var(--green); }
  .shape-red { fill: var(--red); }
  .address-dot { fill: var(--red); }
</style>
</head>
<body>
<svg class="flyer" viewBox="0 0 848 1200" xmlns="http://www.w3.org/2000/svg">
  <defs>
    <linearGradient id="halftone-fade" x1="1" y1="0" x2="0" y2="1">
      <stop offset="0" stop-color="#e4e7e3" stop-opacity="0.8"/>
      <stop offset="0.6" stop-color="#e4e7e3" stop-opacity="0.25"/>
      <stop offset="1" stop-color="#e4e7e3" stop-opacity="0"/>
    </linearGradient>
    <linearGradient id="halftone-fade-low" x1="0" y1="1" x2="1" y2="0">
      <stop offset="0" stop-color="#e4e7e3" stop-opacity="0.75"/>
      <stop offset="1" stop-color="#e4e7e3" stop-opacity="0"/>
    </linearGradient>
    <linearGradient id="photo-tones" x1="0" y1="0" x2="0" y2="1">
      <stop offset="0" stop-color="#5a4a3e"/>
      <stop offset="0.3" stop-color="#d9a98e"/>
      <stop offset="0.6" stop-color="#c9ccc8"/>
      <stop offset="1" stop-color="#4a5566"/>
    </linearGradient>
  </defs>

  <!-- background texture -->
  <rect class="halftone-area" x="0" y="0" width="848" height="620" fill="url(#halftone-fade)" role="img" aria-label="Faint halftone dot pattern"/>
  <rect class="halftone-area" x="0" y="810" width="380" height="390" fill="url(#halftone-fade-low)" role="img" aria-label="Faint halftone dot pattern"/>

  <!-- decorative geometry -->
  <circle class="corner-ring" cx="0" cy="10" r="175" fill="none" stroke="var(--green)" stroke-width="50"/>
  <circle class="shape-green feature-circle" cx="630" cy="770" r="262"/>
  <circle class="shape-green lower-circle" cx="480" cy="1205" r="215"/>

  <!-- brand -->
  <g class="brand">
    <circle class="brand-mark" cx="578" cy="118" r="12"/>
    <text class="type brand-name" x="598" y="133" textLength="205" lengthAdjust="spacingAndGlyphs">Ledgerline</text>
  </g>

  <!-- headline -->
  <g class="headline">
    <text class="type headline-small" x="201" y="154" textLength="283" lengthAdjust="spacingAndGlyphs">Same Day</text>
    <text class="type headline-tax" x="214" y="340" textLength="258" lengthAdjust="spacingAndGlyphs">Tax</text>
    <text class="type headline-advance" x="137" y="418" textLength="411" lengthAdjust="spacingAndGlyphs">Advance up to</text>
    <text class="type headline-amount" x="140" y="578" textLength="405" lengthAdjust="spacingAndGlyphs">$6,000</text>
  </g>

  <!-- offer band -->
  <rect class="shape-red offer-band" x="0" y="618" width="580" height="186"/>
  <text class="type band-intro" x="41" y="699" textLength="419" lengthAdjust="spacingAndGlyphs">File your taxes and apply for an</text>
  <text class="type band-offer" x="123" y="748" textLength="255" lengthAdjust="spacingAndGlyphs">Easy Advance</text>

  <!-- photo area -->
  <path class="photo-area" d="M480 1200 L480 760 Q520 690 630 688 Q740 690 760 760 L848 960 L848 1200 Z" fill="url(#photo-tones)" role="img" aria-label="Photo of a surprised young man holding a fan of fifty-dollar bills in front of his face"/>

  <!-- contact -->
  <text class="type contact-title" x="94" y="855" textLength="238" lengthAdjust="spacingAndGlyphs">Contact Us Today!</text>
  <text class="type contact-phone" x="41" y="926" textLength="345" lengthAdjust="spacingAndGlyphs">(000) 123 4567 890</text>

  <g class="addresses">
    <circle class="address-dot" cx="37" cy="988" r="11"/>
    <text class="type address-line" x="63" y="996" textLength="171" lengthAdjust="spacingAndGlyphs">Address XXXXX XXX XXX</text>
    <circle class="address-dot" cx="37" cy="1038" r="11"/>
    <text class="type address-line" x="63" y="1046" textLength="171" lengthAdjust="spacingAndGlyphs">Address XXXXX XXX XXX</text>
    <circle class="address-dot" cx="37" cy="1092" r="11"/>
    <text class="type address-line" x="63" y="1100" textLength="171" lengthAdjust="spacingAndGlyphs">Address XXXXX XXX XXX</text>
  </g>
</svg>
</body>
</html>
```